Business Card Design - Photographer

I am a landscape photographer and I require a business card design. 

I require two designs:
1)  a double sided business card
 and
b)  a single sided business card 

The single sided design can either be the same as the double sided (with just one side having all the information)....or it can be an entire new design. Its up to you.

My corporate colours are (CMYK):

Blue   69, 32, 0, 0
Grey  72,  64,  47,  31
Green  32,  2,  91,  0
Yellow   0, 19, 92, 0
Orange  0, 39, 75, 0

Colour space in final file should be in CMYK.

The details that need to be included on the card:

- Use the provided Logo
- Name: Wiktor Baranowski
- Email:   sales@vistalumeworks.com.au
- Website:    vistalumeworks.com.au
- Twitter:    twitter.com/vistalumeworks
- Facebook:   facebook.com/vistalumeworks
- Mobile  0417 539 662

Please use the attached template to design the logo to the specified size, including the marked bleed lines. I have also attached my logo in PNG (transparent background) and ai format for you to use.

The final file should be:
- Photoshop version with layers so I can edit the name/text etc. All non vector files should be high resolution at 1039 x 697 pixels at 300 dpi.

I also require a file as:
- Vector based PDF

Anyway questions please contact me.

Thank you

Industry/Entity Type

Landscape

Logo styles of interest
Pictorial/Combination Logo
Abstract Logo
Wordmark Logo
Lettermark Logo
Requirements
Must have
• The details that need to be included on the card:

- Use the provided Logo
- Name: Wiktor Baranowski
- Email: sales@vistalumeworks.com.au
- Website: vistalumeworks.com.au
- Twitter: twitter.com/vistalumeworks
- Facebook: facebook.com/vistalumeworks
- Mobile 0417 539 662

```html
<!DOCTYPE html>
<html lang="en">
<head>
<meta charset="utf-8">
<title>Vistalume Works – Single Sided Business Card</title>
<link rel="stylesheet" href="https://fonts.googleapis.com/css2?family=Ubuntu:wght@400;500;700&display=swap">
<style>
  :root{
    --backdrop:#141414;
    --title:#f2c316;
    --paper:#f4f3f1;
    --ink-dark:#3c3f4a;
    --ink-soft:#707070;
    --brand-blue:#3a8fd0;
    --brand-orange:#f0a03c;
    --brand-yellow:#f2c316;
    --brand-black:#1e1e1e;
    --divider:#b5b5b5;
  }
  *{box-sizing:border-box;margin:0;padding:0}
  html,body{width:1121px;height:1200px;overflow:hidden;background:var(--backdrop)}
  body{position:relative;font-family:"Ubuntu",sans-serif}
  .sheet-title{position:absolute;top:26px;left:0;width:100%;text-align:center;color:var(--title);font-size:28px;font-weight:400;line-height:36px}
  .card{position:absolute;left:267px;width:588px;height:336px;background:var(--paper);border-radius:13px;overflow:hidden;box-shadow:0 4px 14px rgba(0,0,0,.5)}
  .card--one{top:79px;border-top-right-radius:56px}
  .card--two{top:460px}
  .card--three{top:839px;border-top-left-radius:56px}
  .line{position:absolute;white-space:nowrap;line-height:1}
  .brand-mark{position:absolute;width:72px;height:72px;border-radius:50%;background:var(--ink-dark)}
  .brand-name{position:absolute;white-space:nowrap;font-size:21px;font-weight:500;color:var(--ink-dark);line-height:1;letter-spacing:.5px}
  .person{font-size:15px;font-weight:500;color:var(--ink-dark)}
  .contact{font-size:14.5px;color:var(--ink-soft)}
  .web{font-size:15px;color:var(--brand-blue)}
  .social{font-size:13.5px;color:var(--ink-soft);display:flex;align-items:center;gap:4px}
  .social-dot{display:inline-block;width:12px;height:12px;border-radius:2px;background:var(--brand-blue)}
  .social-dot--dark{background:#2c4f8c}
  .divider{position:absolute;left:293px;top:87px;width:1px;height:163px;background:var(--divider)}
  .colour-band{position:absolute;left:0;top:280px;width:100%;height:3px;
    background:linear-gradient(90deg,
      var(--brand-orange) 0 18%, var(--brand-blue) 18% 36.6%, var(--brand-black) 36.6% 44.4%,
      var(--brand-yellow) 44.4% 57.2%, var(--brand-orange) 57.2% 70%, var(--brand-blue) 70% 77.6%,
      var(--brand-yellow) 77.6% 91.1%, var(--brand-black) 91.1% 100%)}
  .right{right:26px;text-align:right}
</style>
</head>
<body>
  <h1 class="sheet-title">single sided business card</h1>

  <section class="card card--one">
    <span class="brand-mark" style="left:425px;top:34px"></span>
    <span class="brand-name" style="right:26px;top:122px">VISTALUME WORKS</span>
    <span class="line person" style="left:25px;top:196px">Wiktor Baranowski</span>
    <span class="line contact" style="left:25px;top:228px">sales@vistalumeworks.com.au</span>
    <span class="line contact" style="left:25px;top:247px">M. 0417 539 662</span>
    <span class="line social" style="left:25px;top:295px"><i class="social-dot"></i>vistalumeworks</span>
    <span class="line social" style="left:161px;top:295px"><i class="social-dot social-dot--dark"></i>vistalumeworks</span>
    <span class="line web right" style="top:294px">www.vistalumeworks.com.au</span>
  </section>

  <section class="card card--two">
    <span class="brand-mark" style="left:124px;top:106px"></span>
    <span class="brand-name" style="left:50px;width:220px;text-align:center;top:194px">VISTALUME WORKS</span>
    <span class="divider"></span>
    <span class="line person right" style="top:130px">Wiktor Baranowski</span>
    <span class="line contact right" style="top:170px">sales@vistalumeworks.com.au</span>
    <span class="line contact right" style="top:189px">M. 0417 539 662</span>
    <span class="line web" style="left:195px;width:208px;text-align:center;top:271px">www.vistalumeworks.com.au</span>
    <span class="line social" style="left:157px;top:293px"><i class="social-dot"></i>vistalumeworks</span>
    <span class="line social" style="left:310px;top:293px"><i class="social-dot social-dot--dark"></i>vistalumeworks</span>
  </section>

  <section class="card card--three">
    <span class="brand-mark" style="left:89px;top:36px"></span>
    <span class="brand-name" style="left:15px;width:220px;text-align:center;top:122px">VISTALUME WORKS</span>
    <span class="line person right" style="top:188px">Wiktor Baranowski</span>
    <span class="line contact right" style="top:223px">sales@vistalumeworks.com.au</span>
    <span class="line contact right" style="top:242px">M. 0417 539 662</span>
    <span class="colour-band"></span>
    <span class="line web" style="left:25px;top:295px">www.vistalumeworks.com.au</span>
    <span class="line social" style="left:306px;top:296px"><i class="social-dot"></i>vistalumeworks</span>
    <span class="line social right" style="top:296px"><i class="social-dot social-dot--dark"></i>vistalumeworks</span>
  </section>
</body>
</html>
```